Construction Company

Design a clutter free business card, it can be double-sided utilizing the logo for VKM Ltd simple with all relevant contact information.

Please also a letterhead design to function for the purposes of invoicing, all mail requirements, with header to be distinctive while the footer ties page together and incorporates all necessary information.

For now, please use generic / dummy text and when a winner is selected, I will disclose the contact information.

Hi Designers! Please read the updated brief which includes the design of a business card and letterhead. Thank you!

```html
<!DOCTYPE html>
<html lang="en">
<head>
<meta charset="utf-8">
<title>VKM Ltd – Business Card</title>
<link rel="stylesheet" href="https://fonts.googleapis.com/css2?family=Roboto:wght@400;500&display=swap">
<style>
  :root {
    --stage: #3c3d3f;
    --royal-blue: #0b3694;
    --royal-blue-light: #1d4fb3;
    --gold: #c9a227;
    --ink-blue: #1f3f8f;
    --paper: #ffffff;
    --rule: #8ea0c8;
  }
  * { box-sizing: border-box; margin: 0; padding: 0; }
  html, body {
    width: 1200px;
    height: 899px;
    overflow: hidden;
  }
  body {
    background: var(--stage);
    font-family: "Roboto", Arial, sans-serif;
    position: relative;
  }
  .card {
    position: absolute;
    top: 295px;
    width: 540px;
    height: 309px;
    overflow: hidden;
  }
  .card--front {
    left: 45px;
    background: linear-gradient(135deg, var(--royal-blue) 0%, var(--royal-blue-light) 60%, var(--royal-blue) 100%);
  }
  .card--back {
    left: 615px;
    background: var(--paper);
  }
  .brand-name {
    position: absolute;
    display: flex;
    align-items: center;
    gap: 12px;
    font-weight: 500;
    font-size: 52px;
    letter-spacing: 1px;
    white-space: nowrap;
  }
  .brand-name__dot {
    width: 22px;
    height: 22px;
    border-radius: 50%;
  }
  .card--front .brand-name { left: 120px; top: 110px; color: var(--paper); }
  .card--front .brand-name__dot { background: var(--gold); }
  .front__website {
    position: absolute;
    right: 110px;
    bottom: 52px;
    color: var(--paper);
    font-size: 14px;
  }
  .card--back .brand-name { left: 48px; top: 118px; font-size: 40px; color: var(--royal-blue); }
  .card--back .brand-name__dot { width: 18px; height: 18px; background: var(--gold); }
  .back__divider {
    position: absolute;
    left: 262px;
    top: 56px;
    width: 1px;
    height: 150px;
    background: var(--rule);
  }
  .contact {
    position: absolute;
    left: 282px;
    top: 52px;
    color: var(--ink-blue);
    font-size: 13px;
    line-height: 1.3;
  }
  .contact__name { color: var(--gold); font-size: 19px; font-weight: 500; }
  .contact__role { margin-bottom: 8px; }
  .contact__address { margin-bottom: 10px; }
  .contact__line { display: flex; align-items: center; gap: 8px; }
  .contact__line svg { width: 12px; height: 12px; fill: none; stroke: var(--gold); stroke-width: 1.6; }
  .swoosh { position: absolute; inset: 0; }
</style>
</head>
<body>
  <section class="card card--front" aria-label="Business card front">
    <div class="brand-name"><span class="brand-name__dot"></span>VKM Ltd</div>
    <p class="front__website">www.yourwebsite.com</p>
  </section>

  <section class="card card--back" aria-label="Business card back">
    <svg class="swoosh" viewBox="0 0 540 309" aria-hidden="true">
      <path d="M225 309 C330 250 450 190 540 160 L540 166 C452 198 340 258 245 309 Z" fill="var(--gold)"/>
      <path d="M285 309 C370 262 460 210 540 182 L540 309 Z" fill="var(--royal-blue)"/>
    </svg>
    <div class="brand-name"><span class="brand-name__dot"></span>VKM Ltd</div>
    <div class="back__divider"></div>
    <div class="contact">
      <p class="contact__name">Daniel Carter</p>
      <p class="contact__role">Manager</p>
      <p class="contact__address">Your address<br>city state, ZIP 0000</p>
      <p class="contact__line">
        <svg viewBox="0 0 12 12"><path d="M2 1.5 L4 1.5 L5 4 L3.8 5 C4.5 6.6 5.5 7.6 7 8.2 L8 7 L10.5 8 L10.5 10 C6 10.5 1.5 6 2 1.5 Z"/></svg>
        123-456-2100
      </p>
      <p class="contact__line">
        <svg viewBox="0 0 12 12"><rect x="1" y="2.5" width="10" height="7"/><path d="M1 2.5 L6 6.5 L11 2.5"/></svg>
        youremail@mailbox.com
      </p>
      <p class="contact__line">
        <svg viewBox="0 0 12 12"><circle cx="6" cy="6" r="4.8"/><path d="M1.2 6 H10.8 M6 1.2 C3.5 4 3.5 8 6 10.8 M6 1.2 C8.5 4 8.5 8 6 10.8"/></svg>
        www.yourwebsite.com
      </p>
    </div>
  </section>
</body>
</html>
```